A start-up named "lumerova" - a clinical research organization needs a new PowerPoint design

We need a new PowerPoint Design (incl. business card and stationery design) for an early-stage start-up named "lumerova" seeking to build an ecosystem/ strategic partner alliances or consortium of committed and active collaborators to guide important components of the clinical trial.

Our ultimate goal is to avoid false neutrals – therapies that have not been and may never be evaluated in clinical trials due to the costs and/ or complexity.

The final design should highlight our patient-centric approach, innovative study design supported with the novel AI platform to make a stronger impact on patient lives.

Please see the attached brief for more details.
Updates

Requesting the proposals on color-coding, business-card designs, clinical research visuals, and icons as well as stationery design.

Target Market(s)

Pharma/ Biotech Executives
Medical Institutions
Clinical Trial Participants (Patients)

Colors
e34398

Requirements
Must have
• Use the Color Version of purple/ magenta logo

```html
<!DOCTYPE html>
<html lang="en">
<head>
<meta charset="utf-8">
<title>lumerova stationery</title>
<link href="https://fonts.googleapis.com/css2?family=Raleway:wght@400;500;700&family=Roboto:wght@300;400&family=Arimo:ital,wght@0,400;0,700;1,400&display=swap" rel="stylesheet">
<style>
  :root {
    --magenta: #e20b83;
    --magenta-deep: #b51e63;
    --wine: #b3195f;
    --ink: #111111;
    --grey-text: #555555;
    --icon-grey: #9a9a9a;
    --band-grey: #878787;
    --backdrop: #e2e2e2;
    --paper: #ffffff;
  }
  * { margin: 0; padding: 0; box-sizing: border-box; }
  html, body { width: 998px; height: 1200px; overflow: hidden; background: var(--backdrop); }
  .canvas { position: relative; width: 998px; height: 1200px; }

  .card { position: absolute; top: 91px; width: 423px; height: 254px; box-shadow: 0 10px 30px rgba(0,0,0,.22); }
  .card-front { left: 79px; background: var(--paper); }
  .card-back { left: 509px; width: 424px; background: linear-gradient(90deg, var(--magenta), var(--magenta-deep)); }

  .holder-name { position: absolute; left: 34px; top: 29px; font: 700 19px/1 "Raleway", sans-serif; color: var(--wine); letter-spacing: .2px; }
  .holder-role { position: absolute; left: 34px; top: 49px; font: 400 16.5px/1 "Raleway", sans-serif; color: #333; }

  .contact-icon { position: absolute; left: 34px; width: 26px; height: 26px; border-radius: 5px; background: var(--icon-grey); }
  .contact-icon svg { display: block; width: 26px; height: 26px; }
  .contact-text { position: absolute; left: 72px; font: 300 7.4px/9.5px "Roboto", sans-serif; color: #444; }

  .card-stripe { position: absolute; left: 0; bottom: 0; width: 100%; height: 12px; background: linear-gradient(90deg, var(--magenta), var(--magenta-deep)); }

  .wordmark { position: absolute; display: flex; align-items: center; gap: 5px; font-family: "Raleway", sans-serif; font-weight: 700; color: var(--wine); letter-spacing: -.5px; }
  .wordmark .dot { display: block; background: currentColor; }
  .card-front .wordmark { left: 221px; top: 111px; font-size: 31px; }
  .card-front .wordmark .dot { width: 9px; height: 9px; }
  .card-back .wordmark { left: 86px; top: 99px; font-size: 50px; color: #fff; }
  .card-back .wordmark .dot { width: 14px; height: 14px; }

  .letterhead { position: absolute; left: 220px; top: 392px; width: 571px; height: 738px; background: var(--paper); box-shadow: 0 10px 30px rgba(0,0,0,.2); font-family: "Arimo", sans-serif; color: var(--ink); }
  .letterhead .wordmark { left: 68px; top: 54px; font-size: 28px; }
  .letterhead .wordmark .dot { width: 8px; height: 8px; }
  .sender { position: absolute; right: 26px; top: 44px; text-align: right; font-size: 9.2px; line-height: 10.8px; }
  .edge-mark { position: absolute; right: 0; top: 33px; width: 10px; height: 63px; background: var(--magenta); }

  .recipient { position: absolute; left: 68px; top: 152px; font-size: 10.4px; line-height: 11.9px; }
  .recipient strong { font-weight: 700; }
  .recipient em { font-style: italic; }
  .letter-date { position: absolute; right: 83px; top: 236px; font-size: 10.4px; }
  .letter-body { position: absolute; left: 68px; top: 285px; width: 437px; font-size: 10.4px; line-height: 17.8px; text-align: justify; }
  .letter-body p + p { margin-top: 17.5px; }

  .signature { position: absolute; left: 68px; top: 528px; width: 108px; height: 24px; background: linear-gradient(90deg, #e8e8e8, #f4f4f4); border-radius: 2px; }
  .signer { position: absolute; left: 68px; top: 566px; font-size: 10.4px; line-height: 18px; }
  .signer strong { font-weight: 700; }

  .footer-band { position: absolute; left: 0; top: 694px; width: 100%; height: 25px; background: var(--band-grey); }
  .footer-band .web { position: absolute; left: 0; top: 0; width: 493px; height: 25px; background: var(--magenta); color: #fff; font: 700 7px/25px "Arimo", sans-serif; padding-left: 74px; letter-spacing: .3px; }
</style>
</head>
<body>
<div class="canvas">

  <section class="card card-front">
    <h1 class="holder-name">NAME SURNAME, PHD</h1>
    <p class="holder-role">Managing partner</p>

    <div class="contact-icon" style="top:94px">
      <svg viewBox="0 0 26 26" aria-hidden="true"><g fill="none" stroke="#fff" stroke-width="1.1"><circle cx="13" cy="13" r="7.5"/><ellipse cx="13" cy="13" rx="3.3" ry="7.5"/><path d="M5.5 13h15M6.6 9.2h12.8M6.6 16.8h12.8"/></g></svg>
    </div>
    <p class="contact-text" style="top:99px">name.surname@lumerova.ch<br>www.lumerova.ch</p>

    <div class="contact-icon" style="top:137px">
      <svg viewBox="0 0 26 26" aria-hidden="true"><path fill="#fff" d="M8.3 6.5c.6-.4 1.3-.3 1.7.3l1.6 2.4c.4.6.2 1.3-.3 1.7l-1 .7c.7 1.8 2.3 3.6 4.1 4.6l.8-.9c.5-.5 1.2-.6 1.7-.2l2.3 1.7c.6.4.7 1.2.2 1.7l-1.1 1.3c-.6.7-1.6.9-2.5.6-4.1-1.4-7.6-5.2-8.6-9.5-.2-.9.1-1.8.8-2.4z"/></svg>
    </div>
    <p class="contact-text" style="top:136px">Office: +41 (0)44 555 20 00<br>Phone: +41 (0)44 555 20 18<br>Mobile: +41 (0)79 555 31 42<br>Fax: +41 (0)44 555 20 01</p>

    <div class="contact-icon" style="top:184px">
      <svg viewBox="0 0 26 26" aria-hidden="true"><path fill="#fff" d="M13 5.5a5 5 0 0 0-5 5c0 3.8 5 10 5 10s5-6.2 5-10a5 5 0 0 0-5-5zm0 7a2 2 0 1 1 0-4 2 2 0 0 1 0 4z"/></svg>
    </div>
    <p class="contact-text" style="top:183px; left:73px">lumerova GmbH<br>Street name 1<br>9999 City name<br>Switzerland</p>

    <div class="wordmark"><span>lumerova</span><span class="dot"></span></div>
    <div class="card-stripe"></div>
  </section>

  <section class="card card-back">
    <div class="wordmark"><span>lumerova</span><span class="dot"></span></div>
  </section>

  <article class="letterhead">
    <div class="wordmark"><span>lumerova</span><span class="dot"></span></div>
    <address class="sender" style="font-style:normal">lumerova GmbH<br>Street name 1<br>9999 City name<br>Switzerland</address>
    <div class="edge-mark"></div>

    <div class="recipient">
      <strong>Martin Keller</strong><br>
      <em>Manager</em><br>
      Name Of Corporation<br>
      101 Street Name<br>
      City, State, 98765
    </div>

    <p class="letter-date">Date, 01 January, 2021</p>

    <div class="letter-body">
      <p>This is a sample letter that has been placed to demonstrate typing remit (Your Company). Letterhead design. When positioned properly, it will serve to work in harmony with all other elements letterhead. This letterhead design is meant to project an image</p>
      <p>This letterhead design is meant project an image of professionalism reliability. By using simple align we have created a very spacious feeling. The simplicity suggest rengththe spaciousness contributes h aesthetics the layout. These basic qualities along with the (Your Company)</p>
      <p>This letterhead design is based on the (Form of your logo) form (Your Company) logo. Each stationery we have created a very spacious feeling. The simplicity suggests strength the spaciousness contribute part of the (Form of your logo).</p>
    </div>

    <div class="signature" role="img" aria-label="Handwritten signature of Daniel Brenner"></div>
    <div class="signer"><strong>Daniel Brenner</strong><br>Manager</div>

    <div class="footer-band"><div class="web">WWW.LUMEROVA.CH</div></div>
  </article>

</div>
</body>
</html>
```